IT Company requires new Business Card design.

Over the years we have had a few different business card designs. We are now due for new cards across the board for all staff. We felt this would be a good time to start fresh with a new design. Our traditional card simply had our details on the front, and a list of services on the back. We don't particularly need the list of services, we have had cards where the only thing on the rear of the card was our logo.
Feel free to be creative, we would like our tag line "Complete IT Management" to appear at some point, doesn't necessarily have to be with the logo.
I have attached samples and drafts of various previous cards we have used over the years.

```html
<!DOCTYPE html>
<html lang="en">
<head>
<meta charset="utf-8">
<title>Harbour Systems – Business Card</title>
<link rel="stylesheet" href="https://fonts.googleapis.com/css2?family=Open+Sans:wght@400;600;700&display=swap">
<style>
  :root {
    --backdrop: #e6e6e4;
    --card: #ffffff;
    --slate: #66747f;
    --slate-dark: #5c6a74;
    --ink: #3f4448;
    --on-slate: #ffffff;
    --card-shadow: 0 6px 18px rgba(0,0,0,0.22);
  }
  * { box-sizing: border-box; margin: 0; padding: 0; }
  html, body {
    width: 1034px;
    height: 1200px;
    overflow: hidden;
    background: var(--backdrop);
    font-family: "Open Sans", Arial, sans-serif;
  }
  .canvas { position: relative; width: 1034px; height: 1200px; }

  .card {
    position: absolute;
    left: 67px;
    width: 900px;
    background: var(--card);
    border-radius: 24px;
    box-shadow: var(--card-shadow);
    overflow: hidden;
  }
  .card--front { top: 69px; height: 514px; }
  .card--back  { top: 629px; height: 511px; }

  /* brand lockup */
  .brand {
    position: absolute;
    left: 0; right: 0;
    display: flex;
    justify-content: center;
    align-items: center;
    gap: 28px;
  }
  .card--front .brand { top: 52px; }
  .card--back .brand { top: 178px; }
  .brand__mark {
    width: 150px; height: 150px;
    background: var(--slate);
  }
  .brand__name {
    color: var(--slate);
    font-weight: 700;
    line-height: 0.98;
    text-transform: uppercase;
  }
  .brand__name span { display: block; }
  .brand__line1 { font-size: 78px; letter-spacing: 1px; }
  .brand__line2 { font-size: 40px; letter-spacing: 1px; }

  /* contact band */
  .contact-band {
    position: absolute;
    top: 262px; left: 0;
    width: 100%; height: 194px;
    background: var(--slate);
    color: var(--on-slate);
  }
  .person {
    position: absolute;
    right: 520px;
    top: 26px;
    text-align: right;
  }
  .person__name { font-size: 26px; font-weight: 700; line-height: 1.2; }
  .person__role { font-size: 20px; line-height: 1.5; margin-bottom: 20px; }
  .person__address { font-size: 20px; line-height: 1.55; font-style: normal; }

  .contact-band__divider {
    position: absolute;
    left: 401px; top: 30px;
    width: 1px; height: 142px;
    background: rgba(255,255,255,0.55);
  }

  .contact-list {
    position: absolute;
    left: 427px; top: 12px;
    list-style: none;
  }
  .contact-list li {
    display: flex;
    align-items: center;
    gap: 12px;
    height: 34.5px;
    font-size: 20px;
  }
  .contact-list svg { width: 22px; height: 22px; flex: none; }

  .tagline {
    position: absolute;
    top: 456px; left: 0; width: 100%; height: 58px;
    display: flex; align-items: center; justify-content: center;
    color: var(--slate-dark);
    font-size: 21px;
    letter-spacing: 4px;
    text-transform: uppercase;
  }

  .web {
    position: absolute;
    left: 0; right: 0; top: 452px;
    text-align: center;
    color: var(--ink);
    font-size: 23px;
    letter-spacing: 1.5px;
  }
</style>
</head>
<body>
<main class="canvas">

  <section class="card card--front" aria-label="Card front">
    <div class="brand">
      <div class="brand__mark"></div>
      <div class="brand__name"><span class="brand__line1">Harbour</span><span class="brand__line2">Systems</span></div>
    </div>

    <div class="contact-band">
      <div class="person">
        <p class="person__name">Daniel Hart</p>
        <p class="person__role">Operation Manager</p>
        <address class="person__address">Unit 4 18 Marlow Street<br>Canning Vale WA 6155</address>
      </div>

      <div class="contact-band__divider"></div>

      <ul class="contact-list">
        <li>
          <svg viewBox="0 0 24 24" aria-hidden="true"><circle cx="12" cy="12" r="11" fill="#fff"/><path d="M8.5 6.5l2 2.5-1.2 1.3c.8 1.7 2.1 3 3.8 3.8l1.3-1.2 2.5 2-1.4 2c-4.6-.4-8.6-4.4-9-9z" fill="#66747f"/></svg>
          08 9355 0148
        </li>
        <li>
          <svg viewBox="0 0 24 24" aria-hidden="true"><rect x="7" y="2" width="10" height="20" rx="2" fill="#fff"/><rect x="9" y="5" width="6" height="9" fill="#66747f"/><circle cx="12" cy="18" r="1.3" fill="#66747f"/></svg>
          0412 508 716
        </li>
        <li>
          <svg viewBox="0 0 24 24" aria-hidden="true"><rect x="7" y="3" width="10" height="6" fill="#fff"/><rect x="3" y="9" width="18" height="9" rx="2" fill="#fff"/><rect x="7" y="15" width="10" height="6" fill="#fff" stroke="#66747f" stroke-width="1.2"/></svg>
          08 9355 0148
        </li>
        <li>
          <svg viewBox="0 0 24 24" aria-hidden="true"><rect x="2" y="6" width="20" height="13" rx="1.5" fill="#fff"/><path d="M3 7l9 7 9-7" fill="none" stroke="#66747f" stroke-width="1.6"/></svg>
          daniel@harboursystems.com.au
        </li>
        <li>
          <svg viewBox="0 0 24 24" aria-hidden="true"><circle cx="12" cy="12" r="10" fill="#fff"/><g fill="none" stroke="#66747f" stroke-width="1.3"><ellipse cx="12" cy="12" rx="4.5" ry="10"/><path d="M2 12h20M4 7h16M4 17h16"/></g></svg>
          www.harboursystems.com.au
        </li>
      </ul>
    </div>

    <p class="tagline">Complete IT Management</p>
  </section>

  <section class="card card--back" aria-label="Card back">
    <div class="brand">
      <div class="brand__mark"></div>
      <div class="brand__name"><span class="brand__line1">Harbour</span><span class="brand__line2">Systems</span></div>
    </div>
    <p class="web">www.harboursystems.com.au</p>
  </section>

</main>
</body>
</html>
```